Corwin Beacon Lighting - Commercial & Residential Landscape Lighting

Landscape Lighting Services & Design: Create a website for our landscape lighting company. We would like the design to be tailored around this description:
Illuminate with Confidence. Designed with Precision. Installed with Care.
Locally and veteran-owned, we take pride in transforming outdoor spaces through innovative lighting solutions tailored to your vision. From landscape and holiday lighting to permanent installations, our effortless process and expert design deliver breathtaking results and lasting curb appeal. Backed by a lifetime warranty and quarterly service options, our commitment to quality and customer satisfaction is unwavering. Try before you buy and experience your home in a whole new light with our complimentary demo kit — see the stunning effects before you decide.
- Also, add in this information as well; Outdoor Lighting not only beautifies spaces but also significantly enhances safety by illuminating your home or business. Beautifully lit entrances deter potential intruders, making your home a safer place for your loved ones. we also offer quarterly service plans to ensure lighting equipment continues to operate & illuminate effectively throughout the year. Also mention we provide free estimates and we are offering a 10% discount to military, veterans, and first responders.

Target Market(s)

Luxury market

Industry/Entity Type

Landscape Lighting - Residential & Commercial Lighting Services

Coding

Coded - Design and coding required

Number of Pages Required

2 page

Colors
00AB8E
00BBA5
67D7C9
C6EFE9
E9F9F6
59FF00
82FF00
B8FF75
E3FFCB
F4FFEA
FFC000
F8CF3A
FAE287
FDF2CF
FEFAEE

Requirements
Must have
• a lead generation button where people can submit their information for us to reach out to them and schedule their free estimate, homepage, about page, contact page, products and services page, user friendly, easy to navigate, and it also must be engaging and eye popping, as well as appealing to the luxury market. Please use colors; verdent green, dark green, ivory, and sunny yellow. Also, include an about page that references our story; Derek is retired Army and he opened a fitness studio in 2017 with his wife Jolene. He has installed low voltage lighting in every home he lived in and for his friends and family over the years and decided to open his own business because he is passionate about beautifying outdoor landscapes and highlighting a properties full potential, not only in the day but at night as well all while providing safety and security for his clients. Having a deep respect for nature and landscaping, he wants to provide the same care and quality to each of his clients as he has in the fitness industry for decades. He believes small businesses are the back bone of America and he's excited to provide a service that is all to often neglected in the design of a home.
Nice to have
• I would like to have a clear intent and purpose, engaging web design, clear call to action, optimized for search engines, mobile friendy design, security measures, credibility indicators

```html
<!DOCTYPE html>
<html lang="en">
<head>
<meta charset="utf-8">
<title>Corwin Beacon Lighting – Residential & Commercial Landscape Lighting</title>
<meta name="viewport" content="width=1200">
<link href="https://fonts.googleapis.com/css2?family=Lato:wght@400;700;900&display=swap" rel="stylesheet">
<style>
:root{
  --forest:#1f3f2b;
  --forest-deep:#173222;
  --ink:#2b2b2b;
  --body:#3d3d3d;
  --amber:#f8a51c;
  --amber-text:#f3a21f;
  --ivory:#f7f7f4;
  --white:#ffffff;
  --footer:#1c1c1c;
  --muted:#cfcfcf;
  --wine:#a3243b;
}
*{box-sizing:border-box;margin:0;padding:0}
html,body{width:1200px;height:4870px;overflow:hidden}
body{font-family:'Lato',sans-serif;color:var(--body);background:var(--white);position:relative}
section,header,footer,.topbar{position:absolute;left:0;width:1200px}
.abs{position:absolute}
.btn{position:absolute;display:flex;align-items:center;justify-content:center;background:var(--amber);color:var(--white);font-size:14px;font-weight:700;height:37px;text-decoration:none}
h2.title{font-size:38px;font-weight:700;color:var(--ink);letter-spacing:-.3px}
.kicker{color:var(--amber-text);font-size:17px;line-height:22px}
.photo{position:absolute}

/* top bar */
.topbar{top:0;height:38px;background:var(--forest);color:var(--white);font-size:12px}
.topbar .offer{left:111px;top:11px}
.topbar .demo{left:773px;top:11px}
.topbar .est{left:954px;top:5px;width:134px;height:28px;background:#3a5545;display:flex;align-items:center;justify-content:center}

/* header */
header{top:38px;height:106px;background:var(--white)}
.brand{left:98px;top:28px;display:flex;align-items:center;gap:8px}
.brand-dot{width:14px;height:14px;border-radius:50%;background:var(--wine)}
.brand-name{font-size:17px;font-weight:900;color:var(--wine);letter-spacing:.5px;line-height:20px;width:130px}
.contact-chip{top:12px;display:flex;align-items:center;gap:12px;font-size:14px;color:var(--ink)}
.chip-ico{width:36px;height:36px;border-radius:50%;background:var(--amber);display:flex;align-items:center;justify-content:center}
.navbar{left:503px;top:60px;width:697px;height:46px;background:var(--amber);clip-path:polygon(22px 0,100% 0,100% 100%,0 100%)}
.navbar a{position:absolute;top:13px;color:var(--white);font-size:14px;text-decoration:none;transform:translateX(-50%)}
.navbar a.active{text-decoration:underline;text-underline-offset:4px}

/* hero */
.hero{top:144px;height:599px;background:linear-gradient(180deg,#1d2b1a 0%,#3d5a2a 45%,#5c7a32 70%,#6b8a3a 100%)}
.hero h1{left:111px;top:128px;font-size:50px;line-height:60px;font-weight:700;color:var(--white)}
.hero p{left:111px;top:330px;font-size:20px;line-height:30px;color:var(--white);width:520px}
.play{left:924px;top:260px;width:76px;height:76px;border-radius:50%;background:var(--amber);display:flex;align-items:center;justify-content:center;box-shadow:0 0 30px rgba(248,165,28,.6)}

/* products */
.products{top:743px;height:958px;background:var(--forest)}
.products .left-bg{left:0;top:0;width:576px;height:958px;background:var(--ivory)}
.products .lawn{left:0;top:467px;width:550px;height:491px;background:linear-gradient(180deg,#5f7d45 0%,#4f7a2f 50%,#6a9a32 100%)}
.products h2{left:111px;top:80px}
.products .kicker{left:111px;top:140px;width:330px}
.products p.lead{left:111px;top:205px;width:345px;font-size:14px;line-height:23px;color:var(--body)}
.card{position:absolute;width:270px;background:var(--white);padding:17px 18px}
.card .thumb{height:207px}
.card h3{font-size:16px;font-weight:700;color:var(--ink);margin-top:20px}
.card p{font-size:13.5px;line-height:22px;margin-top:10px;color:var(--body)}
.card a{display:block;font-size:14px;color:var(--amber-text);margin-top:6px;text-decoration:none}

/* about */
.about{top:1701px;height:571px;background:var(--white);z-index:2}
.about .photo{left:111px;top:87px;width:486px;height:550px;background:linear-gradient(160deg,#0f1f14 0%,#2e5a2a 45%,#4e8a36 70%,#2a4a5a 100%)}
.about h2{left:673px;top:80px}
.about .copy{left:673px;top:152px;width:420px;font-size:15px;line-height:25.5px}
.about .copy p+p{margin-top:22px}

/* demo */
.demo-kit{top:2272px;height:459px;background:linear-gradient(180deg,#1f3f2b,#254731);text-align:center;color:var(--white)}
.demo-kit h2{position:absolute;left:0;width:1200px;top:137px;font-size:38px;font-weight:700;color:var(--white)}
.demo-kit .kicker{position:absolute;left:0;width:1200px;top:197px}
.demo-kit p{position:absolute;left:290px;width:620px;top:237px;font-size:14px;line-height:23px}

/* work */
.work{top:2731px;height:784px;text-align:center}
.work h2{position:absolute;left:0;width:1200px;top:80px}
.work p{position:absolute;left:240px;width:720px;top:152px;font-size:16px;line-height:25px}
.tile{position:absolute;width:233px;height:206px}

/* story */
.story{top:3515px;height:567px}
.story h2{left:111px;top:40px}
.story .copy{left:111px;top:112px;width:415px;font-size:15px;line-height:26px}
.story .copy p+p{margin-top:26px}
.story .photo{left:603px;top:46px;width:485px;height:486px;background:linear-gradient(180deg,#2a3f66 0%,#1e2d3e 45%,#3a4a42 75%,#6d7076 100%)}

/* discount */
.discount{top:4082px;height:363px;text-align:center}
.discount h2{position:absolute;left:0;width:1200px;top:48px}
.discount .kicker{position:absolute;left:350px;width:500px;top:108px}
.discount p{position:absolute;left:300px;width:600px;top:168px;font-size:13.5px;line-height:23px}

/* footer */
footer{top:4445px;height:425px;background:var(--footer);color:var(--white)}
footer h4{position:absolute;top:76px;font-size:20px;font-weight:700}
footer .about-txt{left:111px;top:130px;width:245px;font-size:13.5px;line-height:23px}
footer ul{position:absolute;top:126px;list-style:none;font-size:13.5px}
footer li{height:39px}
.social{left:111px;top:268px;display:flex;gap:14px}
.social span{width:34px;height:34px;border-radius:6px;display:block}
.f-contact{left:612px;top:126px;font-size:13.5px;line-height:22px}
.f-row{position:absolute;left:0;display:flex;gap:22px;width:320px}
footer .rule{left:111px;top:360px;width:977px;height:1px;background:#3a3a3a}
footer .copy{left:0;width:1200px;top:395px;text-align:center;font-size:12px;color:var(--muted)}
</style>
</head>
<body>

<div class="topbar">
  <span class="abs offer">10% Off for Military, Veterans &amp; First Responders</span>
  <span class="abs demo">Complimentary Demo Kit</span>
  <span class="abs est">Free Estimates</span>
</div>

<header>
  <div class="abs brand">
    <span class="brand-dot"></span>
    <span class="brand-name">CORWIN BEACON LIGHTING</span>
  </div>
  <div class="abs contact-chip" style="left:574px">
    <span class="chip-ico"><svg width="16" height="16" viewBox="0 0 24 24" fill="#fff"><path d="M6.6 10.8a15 15 0 0 0 6.6 6.6l2.2-2.2c.3-.3.7-.4 1-.2 1.1.4 2.3.6 3.6.6.6 0 1 .4 1 1V20c0 .6-.4 1-1 1A17 17 0 0 1 3 4c0-.6.4-1 1-1h3.5c.6 0 1 .4 1 1 0 1.3.2 2.5.6 3.6.1.3 0 .7-.2 1z"/></svg></span>
    + 1 888 888 8888
  </div>
  <div class="abs contact-chip" style="left:802px">
    <span class="chip-ico"><svg width="16" height="16" viewBox="0 0 24 24" fill="none" stroke="#fff" stroke-width="2"><rect x="3" y="5" width="18" height="14" rx="1"/><path d="M3 6l9 7 9-7"/></svg></span>
    info@corwinbeaconlighting.com
  </div>
  <nav class="abs navbar">
    <a href="#" class="active" style="left:98px">Home</a>
    <a href="#" style="left:209px">About Us</a>
    <a href="#" style="left:374px">Products and Services</a>
    <a href="#" style="left:546px">Contact Us</a>
  </nav>
</header>

<section class="hero">
  <div class="abs" style="inset:0" role="img" aria-label="Landscaped garden bed at dusk lit by modern bollard path lights"></div>
  <h1 class="abs">Illuminate with Confidence.<br>Designed with Precision.<br>Installed with Care.</h1>
  <p class="abs">Locally and veteran-owned experts in transforming landscapes with breathtaking lighting.</p>
  <a class="btn" href="#" style="left:111px;top:417px;width:199px">Get My Free Estimate</a>
  <div class="abs play"><svg width="26" height="26" viewBox="0 0 24 24" fill="#fff"><path d="M7 4l14 8-14 8z"/></svg></div>
</section>

<section class="products">
  <div class="abs left-bg"></div>
  <div class="abs lawn" role="img" aria-label="Manicured lawn with shaped hedges and tall trees"></div>
  <h2 class="abs title">Products &amp; Services</h2>
  <div class="abs kicker">Illuminate Your Outdoors with Style, Security &amp; Pre</div>
  <p class="abs lead">At Corwin Beacon Lighting, we deliver more than light — we craft ambiance, elevate curb appeal, and enhance safety with every custom installation. Whether you're envisioning elegant landscape lighting, festive holiday displays, or permanent, smart-controlled systems, our solutions are tailored to fit your lifestyle and space.</p>
  <a class="btn" href="#" style="left:111px;top:397px;width:131px;height:36px">View All</a>

  <article class="card" style="left:529px;top:87px">
    <div class="thumb" role="img" aria-label="Modern home facade lit at night" style="background:linear-gradient(180deg,#2d3a6a,#1b2340 60%,#3a3a46)"></div>
    <h3>Landscape Lighting</h3>
    <p>Excepteur sint occaecat cupida non proident, sunt in laborum.</p>
    <a href="#">Read More ...</a>
  </article>
  <article class="card" style="left:818px;top:121px">
    <div class="thumb" role="img" aria-label="Outdoor dining table under string lights" style="background:linear-gradient(180deg,#1d2a24,#3e4a32 55%,#8a6a4a)"></div>
    <h3>Holiday Lighting</h3>
    <p>Excepteur sint occaecat cupida non proident, sunt in laborum.</p>
    <a href="#">Read More ...</a>
  </article>
  <article class="card" style="left:529px;top:476px">
    <div class="thumb" role="img" aria-label="Close-up of a warm ground spotlight at night" style="background:linear-gradient(160deg,#1a1d20,#2a2a26 55%,#6a4a20)"></div>
    <h3>Permanent Installations</h3>
    <p>Excepteur sint occaecat cupida non proident, sunt in laborum.</p>
    <a href="#">Read More ...</a>
  </article>
  <article class="card" style="left:818px;top:510px">
    <div class="thumb" role="img" aria-label="Backyard pathway lights leading to a patio at night" style="background:linear-gradient(180deg,#1f2a38,#24302a 55%,#4a4030)"></div>
    <h3>Quarterly Maintenance Plans</h3>
    <p>Excepteur sint occaecat cupida non proident, sunt in laborum.</p>
    <a href="#">Read More ...</a>
  </article>
</section>

<section class="about">
  <div class="photo" role="img" aria-label="Low path light nestled among leafy plants"></div>
  <h2 class="abs title">About Us</h2>
  <div class="abs copy">
    <p>Locally and veteran-owned, we take pride in transforming outdoor spaces through innovative lighting solutions tailored to your vision. From landscape and holiday lighting to permanent installations, our effortless process and expert design deliver breathtaking results and lasting curb appeal.</p>
    <p>Outdoor Lighting not only beautifies spaces but also significantly enhances safety by illuminating your home or business.</p>
  </div>
  <a class="btn" href="#" style="left:673px;top:450px;width:132px;height:36px">Read More</a>
</section>

<section class="demo-kit">
  <h2>Our Complimentary Demo Kit</h2>
  <div class="kicker">Experience the Transformation — Before You Commit</div>
  <p>See your property in a whole new light with our Complimentary Demo Kit. We'll design and install a temporary lighting setup so you can witness the beauty, safety, and curb appeal firsthand — all at no cost.</p>
  <a class="btn" href="#" style="left:501px;top:338px;width:198px;height:36px">Get My Free Demo Kit</a>
</section>

<section class="work">
  <h2 class="title">Our Work</h2>
  <p>Beautifully lit entrances deter potential intruders, making your home a safer place for your loved ones. we also offer quarterly service plans to ensure lighting equipment continues to operate &amp; illuminate effectively throughout the year.</p>
  <div class="tile" style="left:111px;top:250px;background:linear-gradient(180deg,#9aa2a8,#3c3a34 55%,#2e3a24)" role="img" aria-label="House exterior with lit garden at dusk"></div>
  <div class="tile" style="left:359px;top:250px;background:linear-gradient(180deg,#263224,#3e5a2a 60%,#5a6a34)" role="img" aria-label="Bollard lights along a lawn"></div>
  <div class="tile" style="left:607px;top:250px;background:linear-gradient(180deg,#3a4a5a,#2a2a22 55%,#5a4a28)" role="img" aria-label="Installer adjusting a garden light"></div>
  <div class="tile" style="left:854px;top:250px;background:linear-gradient(180deg,#1e2a22,#3a5a30 55%,#8a9aa0)" role="img" aria-label="Path lights beside a walkway"></div>
  <div class="tile" style="left:111px;top:469px;background:linear-gradient(180deg,#3a3a34,#7a5a3a 45%,#4a6a34)" role="img" aria-label="Lit porch with lavender border"></div>
  <div class="tile" style="left:359px;top:469px;background:linear-gradient(180deg,#4a5a6a,#6a5a3a 50%,#3e5a26)" role="img" aria-label="Home at twilight with lawn lights"></div>
  <div class="tile" style="left:607px;top:469px;background:linear-gradient(180deg,#2a3a24,#5a5a54 55%,#3a4a30)" role="img" aria-label="Stone steps lit with post lights"></div>
  <div class="tile" style="left:854px;top:469px;background:linear-gradient(180deg,#3a5a2a,#6a8a3a 55%,#aaa69a)" role="img" aria-label="Curving gravel path through planted beds"></div>
  <a class="btn" href="#" style="left:537px;top:705px;width:128px;height:37px">View All</a>
</section>

<section class="story">
  <h2 class="abs title">Our Derek</h2>
  <div class="abs copy">
    <p>Derek is retired Army and he opened a fitness studio in 2017 with his wife Jolene. He has installed low voltage lighting in every home he lived in and for his friends and family over the years and decided to open his own business because he is passionate about beautifying outdoor landscapes and highlighting a properties full potential, not only in the day but at night as well all while providing safety and security for his clients.</p>
    <p>Having a deep respect for nature and landscaping, he wants to provide the same care and quality to each of his clients as he has in the fitness industry for decades.</p>
  </div>
  <a class="btn" href="#" style="left:115px;top:513px;width:129px;height:36px">Read More</a>
  <div class="photo" role="img" aria-label="Garden walkway lined with lantern posts and tall cypress trees at twilight"></div>
</section>

<section class="discount">
  <h2 class="title">Hero Discount + No-Cost Consultation</h2>
  <div class="kicker">Free Estimates + 10% Off for Military, Veterans &amp; First Responders</div>
  <p>We're proud to support those who serve. Get a personalized lighting consultation at no cost — plus enjoy 10% off your project as our way of saying thank you.</p>
  <a class="btn" href="#" style="left:448px;top:240px;width:304px;height:37px">Claim Your Free Estimate &amp; Discount</a>
</section>

<footer>
  <h4 style="left:111px">About Us</h4>
  <p class="abs about-txt">Locally and veteran-owned, we take pride in transforming outdoor spaces through innovative lighting solutions tailored to your vision.</p>
  <div class="abs social" aria-label="Social media links">
    <span style="background:var(--amber)"></span>
    <span style="border:2px solid #fff"></span>
    <span style="border:2px solid #fff"></span>
    <span style="border:2px solid #fff"></span>
  </div>

  <h4 style="left:431px">Main Links</h4>
  <ul style="left:431px"><li>Home</li><li>About Us</li><li>Products</li><li>Services</li><li>Contact Us</li></ul>

  <h4 style="left:612px">Contact Us</h4>
  <div class="abs f-contact">
    <div class="f-row" style="top:0"><svg width="18" height="20" viewBox="0 0 24 24" fill="none" stroke="#fff" stroke-width="1.6"><path d="M12 22s7-7 7-12a7 7 0 0 0-14 0c0 5 7 12 7 12z"/><circle cx="12" cy="10" r="2.5"/></svg><span>123, Corwin Beacon Lighting<br>Company Na 12356.</span></div>
    <div class="f-row" style="top:84px"><svg width="18" height="18" viewBox="0 0 24 24" fill="none" stroke="#fff" stroke-width="1.6"><path d="M6.6 10.8a15 15 0 0 0 6.6 6.6l2.2-2.2c.3-.3.7-.4 1-.2 1.1.4 2.3.6 3.6.6.6 0 1 .4 1 1V20c0 .6-.4 1-1 1A17 17 0 0 1 3 4c0-.6.4-1 1-1h3.5c.6 0 1 .4 1 1 0 1.3.2 2.5.6 3.6.1.3 0 .7-.2 1z"/></svg><span>+ 1 888 888 8888</span></div>
    <div class="f-row" style="top:146px"><svg width="18" height="18" viewBox="0 0 24 24" fill="none" stroke="#fff" stroke-width="1.6"><rect x="3" y="5" width="18" height="14" rx="1"/><path d="M3 6l9 7 9-7"/></svg><span>Info@corwinbeaconlighting.com</span></div>
  </div>

  <h4 style="left:954px">Other Links</h4>
  <ul style="left:954px"><li>Support</li><li>FAQs</li><li>Cookies Policy</li><li>Terms &amp; Conditions</li><li>Privacy Policy</li></ul>

  <div class="abs rule"></div>
  <div class="abs copy">Copyright © 2024 Corwin Beacon Lighting. All rights reserved.</div>
</footer>

</body>
</html>
```